New Business Card Design Project

I need a design for business cards, i am an electrical business called "Corvane Electrical and Communications" i need the cards to be double sided with the company logo on the back (attached) the front needs to say my company name, web site, email address, telephone number, and ABN number and electrical license number. I am open to different arrangements of the information but would like the background to be incorporating something electrical or something that looks smart. open to all additional ideas also.

The company colours are orange and grey see logo attached.

Business Name: Corvane Electrical and Communications
Website: corvaneelectricalandcomms.example.com.au
Email: brent@corvaneelectricalandcomms.example.com.au
Telephone(mobile): 0481209736
ABN: 71208349162
Lic No: 418273D

Target Market(s)

Business entities, Project Managers, Accounts, Clients

Industry/Entity Type

Electrician

Contact Information for Business Card

I need a design for business cards, i am an electrical business called "Corvane Electrical and Communications" i need the cards to be double sided with the company logo on the back (attached) the front needs to say my company name

Font styles to use
Serif
Sans Serif

Colors
f37122
5c5c5c

Requirements
Must have
• Must have the Logo on the back open to different ways of it being on the back but had in mind to keep it central but again open to other options
Nice to have
• A real modern cool background that is eye catching yet contemporary
Should not have
• No backgrounds of a light bulb or plug or anything like that

```html
<!DOCTYPE html>
<html lang="en">
<head>
<meta charset="utf-8">
<title>Corvane Electrical and Communications – Business Card</title>
<link rel="stylesheet" href="https://fonts.googleapis.com/css2?family=Open+Sans:wght@400;600;700&display=swap">
<style>
  :root {
    --orange: #f7a21b;
    --ink: #111111;
    --grey: #5c5c5c;
    --paper: #ffffff;
    --stage: #e9e6e1;
    --back-top: #1c1c1c;
    --back-bottom: #050505;
  }
  * { box-sizing: border-box; margin: 0; padding: 0; }
  html, body { width: 1200px; height: 900px; overflow: hidden; }
  body {
    background: var(--stage);
    font-family: "Open Sans", Arial, sans-serif;
    position: relative;
  }
  .card {
    position: absolute;
    width: 640px;
    height: 366px;
    border-radius: 4px;
    overflow: hidden;
    box-shadow: 0 10px 28px rgba(0,0,0,0.18);
  }
  /* Back of card */
  .card-back {
    left: 500px;
    top: 50px;
    background: linear-gradient(160deg, var(--back-top), var(--back-bottom));
    display: flex;
    align-items: center;
    justify-content: center;
  }
  .brand {
    display: flex;
    align-items: center;
    gap: 14px;
  }
  .brand-dot {
    width: 22px;
    height: 22px;
    border-radius: 50%;
    background: var(--orange);
  }
  .brand-name {
    font-weight: 700;
    font-size: 58px;
    letter-spacing: 4px;
    color: var(--paper);
    line-height: 1;
  }
  /* Front of card */
  .card-front {
    left: 60px;
    top: 470px;
    background: var(--paper);
  }
  .front-shapes {
    position: absolute;
    inset: 0;
  }
  .holder {
    position: absolute;
    left: 76px;
    top: 22px;
  }
  .holder-name {
    color: var(--orange);
    font-weight: 700;
    font-size: 18px;
    line-height: 1.2;
  }
  .holder-role {
    color: var(--ink);
    font-size: 13px;
    line-height: 1.3;
  }
  .details {
    position: absolute;
    left: 26px;
    top: 140px;
    font-size: 14px;
    color: var(--ink);
    line-height: 1.45;
  }
  .details .label { color: var(--orange); }
  .contact-line {
    display: flex;
    align-items: center;
    gap: 8px;
  }
  .contact-line svg { width: 12px; height: 12px; flex: none; }
  .card-front .brand {
    position: absolute;
    right: 40px;
    top: 158px;
    gap: 10px;
  }
  .card-front .brand-name {
    color: var(--ink);
    font-size: 44px;
    letter-spacing: 3px;
  }
  .card-front .brand-dot { width: 16px; height: 16px; }
</style>
</head>
<body>

<section class="card card-back" aria-label="Card back">
  <div class="brand">
    <span class="brand-dot"></span>
    <span class="brand-name">CORVANE</span>
  </div>
</section>

<section class="card card-front" aria-label="Card front">
  <svg class="front-shapes" width="640" height="366" viewBox="0 0 640 366" aria-hidden="true">
    <polygon points="16,18 58,18 16,52" fill="var(--orange)"/>
    <polygon points="40,52 58,22 58,52" fill="var(--ink)"/>
    <polygon points="0,258 330,258 312,286 0,286" fill="var(--orange)"/>
    <polygon points="332,292 640,292 640,330 310,330" fill="var(--ink)"/>
  </svg>

  <div class="holder">
    <p class="holder-name">Marcus Ellery</p>
    <p class="holder-role">Director</p>
  </div>

  <div class="details">
    <p><span class="label">ABN:</span> 71208349162</p>
    <p><span class="label">Lic No:</span> 418273D</p>
    <p class="contact-line">
      <svg viewBox="0 0 12 12" aria-hidden="true"><path d="M3 1 L5 3.5 L4 5 Q5.5 7 7 8 L8.5 7 L11 9 L9.5 11 Q4 10 1 2.5 Z" fill="var(--orange)"/></svg>
      0481209736
    </p>
    <p class="contact-line">
      <svg viewBox="0 0 12 12" aria-hidden="true"><rect x="0.5" y="2" width="11" height="8" fill="var(--orange)"/><path d="M0.5 2 L6 7 L11.5 2" stroke="#fff" stroke-width="1" fill="none"/></svg>
      brent@corvaneelectricalandcomms.example.com.au
    </p>
    <p class="contact-line">
      <svg viewBox="0 0 12 12" aria-hidden="true"><circle cx="6" cy="6" r="5.5" fill="var(--orange)"/><path d="M0.5 6 H11.5 M6 0.5 Q3 6 6 11.5 M6 0.5 Q9 6 6 11.5" stroke="#fff" stroke-width="0.8" fill="none"/></svg>
      corvaneelectricalandcomms.example.com.au
    </p>
  </div>

  <div class="brand">
    <span class="brand-dot"></span>
    <span class="brand-name">CORVANE</span>
  </div>
</section>

</body>
</html>
```